SaaS Early tech startup business card design

Unique design for experience ecommerce platform company. the business cards will be used by executive members. conformance with color code is required.

```html
<!DOCTYPE html>
<html lang="en">
<head>
<meta charset="UTF-8">
<title>Velto Business Card</title>
<link rel="stylesheet" href="https://fonts.googleapis.com/css2?family=Montserrat:wght@500;600;700&family=Open+Sans:wght@400;600&display=swap">
<style>
  :root {
    --stage: #2b2b2d;
    --navy: #22223a;
    --paper: #ffffff;
    --teal: #17a892;
    --ocean: #1689a6;
    --ink: #1f1f24;
    --muted: #c9c9d6;
    --rule: #b8b8b8;
  }
  * { margin: 0; padding: 0; box-sizing: border-box; }
  html, body { width: 1200px; height: 1040px; overflow: hidden; }
  body {
    background: var(--stage);
    display: flex;
    flex-direction: column;
    align-items: center;
    justify-content: center;
    gap: 60px;
    font-family: "Open Sans", sans-serif;
  }
  .card {
    width: 640px;
    height: 366px;
    position: relative;
    box-shadow: 0 14px 30px rgba(0,0,0,.45);
  }
  .card-back {
    background: var(--navy);
    border-radius: 70px 0 70px 0;
    display: flex;
    flex-direction: column;
    align-items: center;
    justify-content: center;
  }
  .brand-row { display: flex; align-items: center; gap: 22px; margin-top: 20px; }
  .brand-dot {
    width: 110px; height: 110px; border-radius: 50%;
    border: 2px solid rgba(23,137,166,.25);
  }
  .wordmark {
    font-family: "Montserrat", sans-serif;
    font-weight: 700;
    color: var(--ocean);
    letter-spacing: 2px;
    line-height: 1;
  }
  .card-back .wordmark { font-size: 104px; }
  .back-url {
    margin-top: 46px;
    font-size: 14px;
    letter-spacing: 3px;
    color: var(--muted);
  }
  .card-front {
    background: var(--paper);
    border-radius: 0 70px 0 70px;
    display: flex;
    align-items: center;
  }
  .front-brand {
    width: 50%;
    display: flex;
    justify-content: center;
  }
  .card-front .wordmark { font-size: 86px; }
  .divider {
    width: 1px; height: 220px; background: var(--rule);
  }
  .contact { padding-left: 28px; color: var(--ink); }
  .contact-name {
    font-family: "Montserrat", sans-serif;
    font-weight: 600;
    font-size: 24px;
    color: var(--teal);
    letter-spacing: 1px;
    line-height: 1.1;
  }
  .contact-role { font-size: 16px; margin-bottom: 12px; }
  .contact-line {
    display: flex; align-items: center; gap: 8px;
    font-size: 16px; line-height: 1.5;
  }
  .contact-line svg { width: 15px; height: 15px; flex: none; }
  .contact-address { margin-top: 10px; font-size: 16px; line-height: 1.35; }
</style>
</head>
<body>
  <section class="card card-back">
    <div class="brand-row">
      <span class="brand-dot"></span>
      <span class="wordmark">velto</span>
    </div>
    <p class="back-url">www.veltoapp.com</p>
  </section>

  <section class="card card-front">
    <div class="front-brand"><span class="wordmark">velto</span></div>
    <span class="divider"></span>
    <div class="contact">
      <h1 class="contact-name">DANIEL ROWE</h1>
      <p class="contact-role">Managing Director</p>
      <p class="contact-line">
        <svg viewBox="0 0 16 16" fill="var(--teal)"><path d="M3.5 1l2.5 3-1.5 1.6c.8 1.8 2.2 3.2 4 4L10 8l3 2.5-1.4 2.8C6.5 13 3 9.5 2.7 4.4z"/></svg>
        044-555 210 348
      </p>
      <p class="contact-line">
        <svg viewBox="0 0 16 16" fill="none" stroke="var(--teal)" stroke-width="1.6"><rect x="1.5" y="3.5" width="13" height="9"/><path d="M1.5 3.5l6.5 5 6.5-5"/></svg>
        hello@veltoapp.com
      </p>
      <p class="contact-line">
        <svg viewBox="0 0 16 16" fill="none" stroke="var(--teal)" stroke-width="1.3"><circle cx="8" cy="8" r="6.5"/><ellipse cx="8" cy="8" rx="3" ry="6.5"/><path d="M1.5 8h13M2.5 5h11M2.5 11h11"/></svg>
        www.veltoapp.com
      </p>
      <p class="contact-address">218, Harbour Lane Suite 4<br>60318, Northland</p>
    </div>
  </section>
</body>
</html>
```